Bluefern Business Services needs a new interactive and interesting website

We need an interesting, professional, modern and functional company website for Bluefern Business Services - a young IT Services company based out of Chennai, India.

Bluefern Business Services is a fully owned subsidiary of Marlow Goods, one of the world's leading direct to consumer wine merchant.

We already have a registered company logo which must feature in the website.

We conceive, design, develop, test, implement and support IT solutions across the entire Marlow Goods IT landscape. For ex : We currently run about 25 e-commerce websites for Marlow Goods on ATG and Dot Net.

We would like to see our corporate colors used in the website. (Burgundy wine and wine green - source: www.bluefernbs-site.com)

We are looking at this website to communicate a fun, friendly and professionally managed company - reaching out to career seekers, prospective customers and general public.

For reference - The company name 'Bluefern' is an inspiration from the Marlow Goods lineage.

The second image with the world map is stickered on our main entrance to the office, I am not sure where this can be used -just putting it out there..

Please note that there are only a few more days to submit designs for this contest  !

I would appreciate if you can help posting your designs in time for our review and consideration.

Thanks.

Reason: Thanks for your inputs. We have a number of designers and a lot to digest and work with in the past few days. There has been a rush of new designs in the last few days Hence we will require more time to process these and make our decision. Hence i am requesting the contest to be open for more days. Regards, Tarun

Target Market(s)

Prospective job seekers who want to know more about the company and also wish to apply for a job vacancy
People wanting to know more about the company in general and our progress
People who want to see what we offer and how we can help them too - prospective customers
Companies that are interested in our IT Captive journey and are looking for a business opportunity

Industry/Entity Type

E-Commerce

Requirements
Must have
• Log In/ Register facility acting as a Single Sign on for Intranet (Employees)

Facility to post job vacancies (with an expiry date) and enable people to apply for a role and upload their CV/Resume.

Facility to Review Job applications

Facility for website visitors to contact Bluefern business Services via an online 'Contact Us' form with a split of job seekers and business opportunities

Gallery facility to upload pictures regarding company events
Nice to have
• Less Cluttered and contemporary design
Some Wine/Vineyard inspirations will be good but not too much, the company is an IT services company

```html
<!DOCTYPE html>
<html lang="en">
<head>
<meta charset="utf-8">
<title>Bluefern Business Services</title>
<link href="https://fonts.googleapis.com/css2?family=Source+Sans+3:wght@400;600;700&family=PT+Sans+Narrow&display=swap" rel="stylesheet">
<style>
:root{
  --burgundy:#8a0a45;
  --burgundy-dark:#6e0836;
  --grey-text:#555;
  --grey-mid:#777;
  --circle:#6f6f6f;
  --nav-top:#f4f4f4;
  --nav-bottom:#cfcfcf;
  --band:#f2f2f2;
  --footer:#dadada;
  --white:#fff;
  --social:#3d6aa6;
}
*{margin:0;padding:0;box-sizing:border-box}
html,body{width:973px;height:1200px;overflow:hidden}
body{position:relative;background:var(--white);font-family:"Source Sans 3",sans-serif;color:var(--grey-text)}
.abs{position:absolute}
.header{left:0;top:0;width:973px;height:58px;background:var(--burgundy)}
.brand{left:183px;top:6px;color:var(--white);display:flex;gap:6px;align-items:flex-start}
.brand-dot{width:18px;height:18px;border-radius:50%;background:var(--white);margin-top:7px}
.brand-name{font-size:27px;font-weight:700;line-height:26px}
.brand-sub{font-size:16px;line-height:16px;display:block;font-weight:400}
.nav{left:0;top:58px;width:973px;height:42px;background:linear-gradient(var(--nav-top),var(--nav-bottom))}
.nav-item{top:70px;font-size:12px;color:#333}
.nav-active{left:204px;top:58px;width:69px;height:40px;background:linear-gradient(#fff,#e6e6e6);box-shadow:0 0 3px rgba(0,0,0,.3)}
.hero{left:124px;top:98px;width:725px;height:253px;background:linear-gradient(90deg,#f0f0f0,#f7f7f7)}
.hero-photo{left:124px;top:98px;width:300px;height:253px;background:linear-gradient(135deg,#7fae4a 0%,#c9b5a0 40%,#3b4452 100%)}
.hero-vine{left:615px;top:98px;width:234px;height:90px;background:linear-gradient(200deg,#8dbb55,rgba(240,240,240,0))}
.hero-line1{left:455px;top:188px;font-family:"PT Sans Narrow",sans-serif;font-size:23px;color:#555}
.hero-line2{left:455px;top:212px;font-size:31px;font-weight:700;color:var(--burgundy);line-height:32px;width:330px}
.hero-amp{font-size:22px;color:#555;font-weight:400}
.slide-dot{top:324px;width:17px;height:16px;border:1px solid #ccc;border-radius:4px;background:#fff}
.panel{left:123px;top:351px;width:726px;height:537px;background:var(--white);box-shadow:0 0 6px rgba(0,0,0,.08)}
.title{font-size:24px;color:var(--burgundy);line-height:26px;font-weight:400}
.thumb{border:1px solid #bbb}
.subtitle{font-size:24px;color:#777;line-height:26px;font-weight:400}
.copy{font-size:8.6px;line-height:15.6px;color:#444;text-align:justify}
.more{font-size:9px;color:var(--burgundy);display:flex;align-items:center;gap:6px}
.list{list-style:none;font-size:7.6px;line-height:15.6px;color:#222}
.list li::before{content:"\2192";color:var(--burgundy);margin-right:4px}
.quote{font-size:34px;color:#555;font-weight:700;line-height:30px}
.testimonial{font-size:7.6px;line-height:15.6px;color:#444;text-align:justify;width:144px}
.accent{color:var(--burgundy)}
.pager{width:16px;height:16px;border-radius:50%;background:#c4c4c4;display:flex;align-items:center;justify-content:center}
.divider{left:162px;top:641px;width:635px;height:1px;background:#aaa}
.video{left:162px;top:692px;width:264px;height:164px;background:#111}
.video-scene{left:173px;top:704px;width:237px;height:136px;background:linear-gradient(160deg,#6c7f8c,#3a3f4a 60%,#2b2b2b)}
.video-bar{left:162px;top:841px;width:264px;height:15px;background:#222}
.date{width:58px;height:58px;border-radius:50%;background:var(--circle);color:#fff;font-size:15px;line-height:17px;text-align:center;padding-top:12px}
.job-title{font-size:7.4px;color:#222}
.job-text{font-size:7px;color:#666}
.job-more{font-size:7px;color:var(--burgundy)}
.clients{left:0;top:888px;width:973px;height:88px;background:var(--band);border-top:1px solid #ddd}
.client{top:920px;width:110px;text-align:center;font-size:16px;color:#666;line-height:16px;font-weight:600}
.client small{display:block;font-size:7px;letter-spacing:1px;font-weight:400;margin-top:2px}
.footer{left:0;top:976px;width:973px;height:164px;background:var(--footer)}
.foot-title{font-size:16px;color:#222;font-weight:600}
.social{left:198px;width:68px;height:17px;border-radius:2px;background:linear-gradient(#5a86c2,var(--social));color:#fff;font-size:8.5px;display:flex;align-items:center;gap:10px;padding-left:6px}
.social i{width:9px;height:9px;background:#fff;display:block}
.contact{font-size:7.2px;color:#222;line-height:9.2px}
.contact b{color:var(--burgundy);font-weight:400;font-size:8px}
.field{left:624px;width:152px;background:#fff;border:1px solid #ccc;border-radius:3px;font-size:8px;color:#aaa;font-style:italic;padding:3px 5px}
.submit{left:630px;top:1105px;width:38px;height:15px;background:#111;color:#fff;font-size:8.5px;text-align:center;line-height:15px;border-radius:2px}
.bottom{left:0;top:1140px;width:973px;height:60px;background:var(--burgundy-dark)}
.bottom-text{top:1169px;font-size:7.8px;color:#fff}
</style>
</head>
<body>
<header class="abs header"></header>
<div class="abs brand"><span class="brand-dot"></span><div class="brand-name">bluefern<span class="brand-sub">Business Services</span></div></div>

<nav class="abs nav"></nav>
<div class="abs nav-active"></div>
<span class="abs nav-item" style="left:226px">Home</span>
<span class="abs nav-item" style="left:293px">About us</span>
<span class="abs nav-item" style="left:378px">Clients</span>
<span class="abs nav-item" style="left:453px">Services</span>
<span class="abs nav-item" style="left:537px">Careers</span>
<span class="abs nav-item" style="left:636px">Contact us</span>

<section class="abs hero"></section>
<div class="abs hero-photo" role="img" aria-label="Smiling businessman framed by grapevine leaves"></div>
<div class="abs hero-vine" role="img" aria-label="Grapevine leaves"></div>
<div class="abs hero-line1">Emerging provider of global</div>
<div class="abs hero-line2">IT consulting <span class="hero-amp">&amp;</span> Software services !</div>
<span class="abs slide-dot" style="left:586px"></span>
<span class="abs slide-dot" style="left:610px"></span>
<span class="abs slide-dot" style="left:636px"></span>

<section class="abs panel"></section>

<h2 class="abs title" style="left:160px;top:383px">WELCOME !</h2>
<div class="abs thumb" style="left:195px;top:419px;width:111px;height:74px;background:linear-gradient(135deg,#f2f2f2,#9a9a9a)" role="img" aria-label="Hand on a computer mouse beside a keyboard"></div>
<h3 class="abs subtitle" style="left:160px;top:500px">Delivering IT Excellence</h3>
<p class="abs copy" style="left:160px;top:526px;width:228px">Welcome to Bluefern Business Services, an emerging provider of global IT consulting and software services. We are part of the Marlow Goods group, a family run business and the world's largest multi-channel home delivery wine merchant.</p>
<a class="abs more" style="left:318px;top:597px">READ MORE <svg width="20" height="6"><path d="M0 3H18M14 0L19 3L14 6" stroke="#8a0a45" fill="none"/></svg></a>

<h2 class="abs title" style="left:433px;top:386px">WHAT WE DO</h2>
<div class="abs thumb" style="left:453px;top:419px;width:101px;height:73px;background:linear-gradient(135deg,#e8eef3,#8b97a4)" role="img" aria-label="Colleagues discussing work at a laptop"></div>
<ul class="abs list" style="left:434px;top:521px">
<li>Packaged Applications</li>
<li>Enterprise Application Integration</li>
<li>Digital Commerce</li>
<li>Application Development &amp; Maintenance</li>
</ul>
<a class="abs more" style="left:506px;top:597px">READ MORE <svg width="20" height="6"><path d="M0 3H18M14 0L19 3L14 6" stroke="#8a0a45" fill="none"/></svg></a>

<h2 class="abs title" style="left:653px;top:381px">Testimonials</h2>
<div class="abs quote" style="left:655px;top:414px">&ldquo;</div>
<p class="abs testimonial" style="left:668px;top:441px">I've always been pleased with <span class="accent">BLUE FERN</span> Business service because their people are very supportive and are always willing to listen. I also feel that <span class="accent">BLUE FERN</span> Business Service understands our needs as independently.</p>
<p class="abs testimonial" style="left:663px;top:543px">- Dana Whitfield, Ridgecrest, Ohio</p>
<div class="abs quote" style="left:791px;top:548px">&rdquo;</div>
<span class="abs pager" style="left:751px;top:590px"><svg width="6" height="6"><path d="M1 0L6 3L1 6Z" fill="#8a0a45"/></svg></span>
<span class="abs pager" style="left:769px;top:590px"><svg width="6" height="6"><path d="M5 0L0 3L5 6Z" fill="#8a0a45"/></svg></span>

<div class="abs divider"></div>

<h2 class="abs title" style="left:158px;top:654px">Events</h2>
<div class="abs video"></div>
<div class="abs video-scene" role="img" aria-label="Event video: team seated at a conference table"></div>
<div class="abs video-bar"><svg width="264" height="15"><rect x="0" y="0" width="75" height="2" fill="#c00"/><path d="M8 5L13 8L8 11Z" fill="#ddd"/><rect x="190" y="7" width="30" height="2" fill="#c00"/></svg></div>

<h2 class="abs title" style="left:512px;top:654px">Opportunities</h2>
<div class="abs date" style="left:496px;top:688px">26<br>Nov</div>
<div class="abs job-title" style="left:558px;top:704px">Software Developers/Programmer Analysts</div>
<div class="abs job-text" style="left:558px;top:722px">AX We are looking for a AX Software Developer to join...</div>
<div class="abs job-more" style="left:560px;top:732px">read more &gt;&gt;</div>
<div class="abs date" style="left:500px;top:754px">28<br>Nov</div>
<div class="abs job-title" style="left:564px;top:770px">Software Developers/Programmer Analysts</div>
<div class="abs job-text" style="left:564px;top:788px">AX We are looking for a AX Software Developer to join...</div>
<div class="abs job-more" style="left:566px;top:798px">read more &gt;&gt;</div>
<span class="abs pager" style="left:758px;top:823px"><svg width="6" height="6"><path d="M1 0L6 3L1 6Z" fill="#8a0a45"/></svg></span>
<span class="abs pager" style="left:777px;top:823px"><svg width="6" height="6"><path d="M5 0L0 3L5 6Z" fill="#8a0a45"/></svg></span>

<section class="abs clients"></section>
<h2 class="abs" style="left:133px;top:895px;font-size:18px;font-weight:400;color:#222">Clients</h2>
<svg class="abs" style="left:164px;top:926px" width="12" height="14"><path d="M11 0L1 7L11 14" fill="#aaa"/></svg>
<svg class="abs" style="left:801px;top:926px" width="12" height="14"><path d="M1 0L11 7L1 14" fill="#aaa"/></svg>
<div class="abs client" style="left:185px">Hartwell's<small>WINE</small></div>
<div class="abs client" style="left:311px">Ember Cellars</div>
<div class="abs client" style="left:438px">Marlow Goods</div>
<div class="abs client" style="left:558px">The Weekend Cellar Club</div>
<div class="abs client" style="left:672px">Ashgroves<small>FINE MERCHANTS</small></div>

<footer class="abs footer"></footer>
<h3 class="abs foot-title" style="left:198px;top:998px">Follow Us</h3>
<div class="abs social" style="top:1028px"><i></i>Pagebook</div>
<div class="abs social" style="top:1051px"><i></i>Workline</div>

<h3 class="abs foot-title" style="left:355px;top:999px">GET IN TOUCH WITH US</h3>
<div class="abs contact" style="left:357px;top:1028px"><b>Address:</b> Bluefern Business Services Pvt. Ltd.</div>
<div class="abs contact" style="left:402px;top:1038px">4th Floor, Harbor Point Tower Unit C12<br>Lakeview Industrial Estate Velmur<br>Chennai, 600099 &nbsp; Tamil Nadu</div>
<svg class="abs" style="left:356px;top:1073px" width="9" height="9"><path d="M1 1L3 0L5 3L3.5 4.5Q4.5 6.5 5 7L6.5 5.5L9 7.5L8 9Q2 8 1 1Z" fill="#555"/></svg>
<div class="abs contact" style="left:372px;top:1074px"><b>Phone:</b> +91 (44) 55501234</div>
<svg class="abs" style="left:356px;top:1092px" width="10" height="8"><rect x="0.5" y="0.5" width="9" height="7" fill="none" stroke="#555"/><path d="M0.5 0.5L5 4.5L9.5 0.5" fill="none" stroke="#555"/></svg>
<div class="abs contact" style="left:370px;top:1092px"><b>E-mail:</b> contactus@bluefernbs-site.com</div>

<h3 class="abs foot-title" style="left:624px;top:994px">Quick Message</h3>
<div class="abs field" style="top:1018px;height:19px">Your email</div>
<div class="abs field" style="top:1040px;height:59px">Message</div>
<div class="abs submit">Submit</div>

<div class="abs bottom"></div>
<div class="abs bottom-text" style="left:181px">Copyright Bluefern Business Services Private Limited.</div>
<div class="abs bottom-text" style="left:622px">Home &nbsp;&nbsp;| &nbsp;&nbsp;About us | &nbsp;Service | &nbsp;Gallery &nbsp;| Contact us</div>
</body>
</html>
```